2 x Digitize Logo | 2 x Business Cards | 2 x Fridge Magnets

We require 6 deliverables:
1. Residential logo redrawn (same just high quality for large print format).
2. Corporate logo redrawn (minor changes to wording and high quality for large print format).
3. New business card design for Furniture Removals (residential)
4. New business card design for Corporate Relocations (business)
5. New Fridge magnet for Furniture removals (residential)
6. New fridge magnet for Corporate Relocations (business)
1. Residential Logo
a. We require the logo to be translated into a high quality digital image with no modifications.
(see attached resilogo.jpg)
2. Residential Logo
a. We require the logo to be edited (add the word corporate relocations) be translated into a high quality digital image.
(see attached corplogo.jpg)
3. Using the resilogo please make a new business card for our business.
a. Please see the web site https://www.larkbendcarters.com.au for colours and inspiration.
b. The residential business card needs the following information:
i. Business Name (using the residential logo).
ii. Free Call: 1800 LB Cart (the L, B and Cart much be the same colour as the logo).
iii. Website: www.LarkbendCarters.com.au
iv. Address: 4/17 Ormsdale Court, VIC 3264
v. Email: cart@LarkbendCarters.com.au
vi. backof Card:
Review our service
www.PennantOrbit.com.au
Services: Local, Country, Interstate | Furniture Removals | Piano, Billiard Tables & Antiques
4. Using the corplogo please make a new business card for our business.
b. The corporate business card needs the following information:
i. Business Name (using the corporate logo).
v. Email: corporate@LarkbendCarters.com.au
vi. Back of Card:
Review our service
www.PennantOrbit.com.au
Services: Corporate relocations | Office equipment moves | Packing Service | Packing Materials
5. Using the resilogo please make a new fridge magent for our business.
b. The residential fidge magnet needs the following information:
iv. Services: Local, Country, Interstate | Furniture Removals | Piano, Billiard Tables & Antiques
6. Using the corplogo please make a new fridge magent for our business.
b. The corporate fidge magnet needs the following information:
iv. Services: Local, Country, Interstate | Corporate relocations
Target Market(s)
Residential Furniture Removals and Corporate Office relocations
Industry/Entity Type
Business
Contact Information for Business Card
Please see full brief for six items required
Requirements
Must have
- Clean simple, easy to read
Nice to have
- fresh, stand out, eye catching
Should not have
- plain, standard, boring, general

```html
<!DOCTYPE html>
<html lang="en">
<head>
<meta charset="utf-8">
<title>Larkbend Carters – Business Card</title>
<link href="https://fonts.googleapis.com/css2?family=Source+Sans+3:wght@400;600;800&display=swap" rel="stylesheet">
<style>
  :root {
    --brand-green: #22b14c;
    --brand-red: #ed1c24;
    --brand-yellow: #fdc20e;
    --ink: #2b2b2b;
    --paper: #ffffff;
    --backdrop: #ecebe8;
    --font-body: "Source Sans 3", "Myriad Pro", Arial, sans-serif;
  }
  * { box-sizing: border-box; margin: 0; padding: 0; }
  html, body { width: 1200px; height: 900px; overflow: hidden; }
  body {
    background: var(--backdrop);
    font-family: var(--font-body);
    display: flex;
    flex-direction: column;
    align-items: center;
    justify-content: center;
    gap: 56px;
  }
  .card {
    position: relative;
    width: 640px;
    height: 366px;
    box-shadow: 0 6px 18px rgba(0,0,0,0.18);
    overflow: hidden;
  }

  /* Back of card */
  .card--back {
    background: var(--brand-green);
    color: var(--paper);
    text-align: center;
    padding-top: 72px;
  }
  .review-label { font-size: 17px; font-weight: 400; }
  .review-link {
    display: block;
    color: var(--brand-red);
    font-size: 21px;
    text-decoration: none;
    margin-top: 2px;
  }
  .services-heading {
    display: flex;
    align-items: center;
    justify-content: center;
    gap: 14px;
    margin: 18px auto 12px;
    font-size: 17px;
    text-transform: uppercase;
  }
  .services-heading::before,
  .services-heading::after {
    content: "";
    width: 150px;
    height: 1px;
    background: var(--paper);
  }
  .services-list { list-style: none; font-size: 18px; line-height: 1.3; text-transform: uppercase; }

  /* Front of card */
  .card--front { background: var(--paper); color: var(--ink); }
  .brand {
    position: absolute;
    left: 58px;
    top: 62px;
    display: flex;
    align-items: center;
    gap: 12px;
  }
  .brand-dot { width: 18px; height: 18px; border-radius: 50%; background: var(--brand-red); }
  .brand-name {
    font-size: 38px;
    font-weight: 800;
    letter-spacing: 1px;
    text-transform: uppercase;
    color: var(--brand-green);
  }
  .contact-list {
    position: absolute;
    left: 58px;
    top: 170px;
    list-style: none;
    font-size: 21px;
    line-height: 31px;
  }
  .contact-item { display: flex; align-items: center; gap: 12px; }
  .contact-icon { width: 17px; height: 17px; flex: none; fill: var(--brand-red); }
  .contact-item a { color: inherit; text-decoration: none; }
  .hl-yellow { color: var(--brand-yellow); }
  .hl-red { color: var(--brand-red); }
  .hl-green { color: var(--brand-green); }

  .colour-band {
    position: absolute;
    left: 0; right: 0; bottom: 0;
    height: 24px;
    display: flex;
  }
  .colour-band span { height: 100%; }
  .band-yellow { width: 45%; background: var(--brand-yellow); }
  .band-red { width: 29%; background: var(--brand-red); }
  .band-green { width: 26%; background: var(--brand-green); }
</style>
</head>
<body>

<section class="card card--back" aria-label="Back of business card">
  <p class="review-label">Review Our Service</p>
  <a class="review-link" href="https://www.pennantorbit.com.au">www.PennantOrbit.com.au</a>
  <p class="services-heading">Services</p>
  <ul class="services-list">
    <li>Local, Country, Interstate</li>
    <li>Furniture Removals</li>
    <li>Piano, Billiard Tables &amp; Antiques</li>
  </ul>
</section>

<section class="card card--front" aria-label="Front of business card">
  <div class="brand">
    <span class="brand-dot"></span>
    <span class="brand-name">Larkbend Carters</span>
  </div>

  <ul class="contact-list">
    <li class="contact-item">
      <svg class="contact-icon" viewBox="0 0 24 24" aria-hidden="true"><path d="M6.6 10.8a15.1 15.1 0 0 0 6.6 6.6l2.2-2.2a1 1 0 0 1 1-.25 11.4 11.4 0 0 0 3.6.57 1 1 0 0 1 1 1V20a1 1 0 0 1-1 1A17 17 0 0 1 3 4a1 1 0 0 1 1-1h3.5a1 1 0 0 1 1 1c0 1.25.2 2.45.57 3.57a1 1 0 0 1-.25 1z"/></svg>
      <span>1800 <span class="hl-yellow">L</span><span class="hl-red">B</span> <span class="hl-green">Cart</span> / 1800 52 48 19</span>
    </li>
    <li class="contact-item">
      <svg class="contact-icon" viewBox="0 0 24 24" aria-hidden="true"><path d="M2 5h20v14H2z M3.5 6.5 12 13l8.5-6.5" fill="var(--brand-red)"/><path d="M3.5 6.8 12 12.8l8.5-6" fill="none" stroke="#fff" stroke-width="1.6"/></svg>
      <a href="mailto:cart@LarkbendCarters.com.au">cart@LarkbendCarters.com.au</a>
    </li>
    <li class="contact-item">
      <svg class="contact-icon" viewBox="0 0 24 24" aria-hidden="true"><circle cx="12" cy="12" r="10"/><path d="M2 12h20M12 2c3 3 3 17 0 20M12 2c-3 3-3 17 0 20" fill="none" stroke="#fff" stroke-width="1.5"/></svg>
      <a href="https://www.larkbendcarters.com.au">www.LarkbendCarters.com.au</a>
    </li>
    <li class="contact-item">
      <svg class="contact-icon" viewBox="0 0 24 24" aria-hidden="true"><path d="M12 2a7 7 0 0 0-7 7c0 5.2 7 13 7 13s7-7.8 7-13a7 7 0 0 0-7-7zm0 9.5A2.5 2.5 0 1 1 12 6.5a2.5 2.5 0 0 1 0 5z"/></svg>
      <span>4/17 Ormsdale Court, VIC 3264</span>
    </li>
  </ul>

  <div class="colour-band" aria-hidden="true">
    <span class="band-yellow"></span>
    <span class="band-red"></span>
    <span class="band-green"></span>
  </div>
</section>

</body>
</html>
```